Lotstallmart.com Webpage Design

Design Brief for lotstallmart.com (Copy of Brief also in attached Word file)

Name of Website- lotstallmart.com (existing logo and look & feel of website to be changed)

Logo - Finalised. The logo files are attached with the brief as “logo.jpeg”. The “Blue- Grey” version of the logo is for use on lighter backgrounds and the “Orange-White” version of the logo is for use on darker backgrounds. (A full Black version of the logo is also attached). Both versions may be used in different parts of the website. All attached files are in .png format.
Status - The website in functional and is undergoing user trials. However, we want to improve the look & feel of the website so at it seems
a. cotemporary,
b. Easy to Navigate
c. professional and
d. Vibrant.

Please visit ‘lotstallmart.com’ to check out the website and its functionalities – please use it only as a reference for the features & functions to be provided, however the designer should use a ‘Free Hand’ in designing the composition of various parts of the webpage without getting too influenced by the existing design

Objective of the Website ‘lotstallmart.com –
a. It is a portal focussed on listing of ‘Retail’ specific real-estate properties by developers, owners and realty brokers. The properties shall listed under the following four categories-
i. Retail Malls
ii. Shopping Complexes
iii. High-street shops
iv. Retail Warehouses
*refer lotstallmart.com for better clarity

b. The abovementioned properties shall be listed either for ‘Sale’ or ‘rent\lease’ or both

c. Users shall visit the site in case they wish to acquire a retail \ shop space either on ‘sale’ or ‘rent’. These Users would be able to specify the ‘Search Criteria’ through the tool-bars provided on the website – the ‘Search Criteria’ shall comprise of ‘Type of space category’, ‘City’, ‘Locality’, transaction type ie ‘Rent \ Sale’ and ‘Area Range’

d. The main revenue model for the website shall be listing fee ( or advertising charges ) payable by those listing their properties on the website.

Three Main Pages of Website (lotstallmart.com) that need to be designed -
a. Main Home Page (visit the web link - http://lotstallmart.com/ ) - The main home page has the “Search Toolbar” for specifying of Search Criteria by the User. It shall also have the following features & functions-
i. Main Advertising Banner
ii. Featured Projects
iii. New Launches
iv. Toolbar with buttons – ‘Advertise with Us’, ‘Listings Alert’, ‘Mart Wizards’, ‘Advertiser Login’

b. Property Listings Page (visit the web link - http://lotstallmart.com/gurgaon-in-india ) - The List of property options that match the Criteria specified by the ‘User’ get displayed on this page.

c. Property Detail Page - When the ‘User’ clicks on the “More….” Button on the ‘Property Listings Page’ (given in point b. above) the web page with the details of the property opens. (For Example – visit the web link - http://lotstallmart.com/vorne-Shopping-Complex-vorne-quadrion-gurgaon-636 )

Note:- Please refer to attached ‘Shopping’ related images the designer may use them on the website to provide a look & feel of retail if required – either separately or rotate in a single window

Target Market(s)

Retailers & Investors looking for retail space, Real Estate Brokers, Developers

Industry/Entity Type

Advertising

Number of Pages Required

3 page

Requirements
Must have
• Refer to existing site lotstallmart.com -- all the existing functionalities are a must have.
Nice to have
• The Designer may use the retail related images on the website if required for making it more vibrant. Refer attached images Shopping(1-6).jpg

```html
<!DOCTYPE html>
<html lang="en">
<head>
<meta charset="utf-8">
<title>lotstallmart.com – Home</title>
<link href="https://fonts.googleapis.com/css2?family=Open+Sans:wght@400;600;700&display=swap" rel="stylesheet">
<style>
:root{
  --blue:#1a7fc4;
  --blue-btn:#1b8fd8;
  --ink:#3b3b3b;
  --muted:#8a8a8a;
  --card:#f2f2f2;
  --btn-dark:#505050;
  --band:#ececec;
  --enquiry:#3a3a3a;
  --footer:#232323;
  --footer-base:#1a1a1a;
  --footer-text:#a8a8a8;
  --white:#ffffff;
}
*{margin:0;padding:0;box-sizing:border-box}
html,body{width:1200px;height:2384px;overflow:hidden}
body{position:relative;background:var(--white);font-family:"Open Sans",Arial,sans-serif;color:var(--ink)}
.abs{position:absolute}

/* header */
.site-header{left:0;top:0;width:1200px;height:108px;background:var(--white)}
.brand{left:98px;top:34px;display:flex;align-items:center;gap:10px}
.brand-dot{width:30px;height:30px;border-radius:50%;background:var(--blue)}
.brand-name{font-size:25px;font-weight:700;color:var(--blue);letter-spacing:-0.3px}
.brand-tag{left:140px;top:68px;font-size:7px;font-weight:700;color:#555;letter-spacing:.4px}
.main-nav{top:33px;left:0;height:32px}
.nav-link{position:absolute;top:0;line-height:32px;font-size:12px;font-weight:600;color:#444;white-space:nowrap}
.nav-link.active{color:var(--blue)}
.nav-login{position:absolute;left:971px;top:0;width:130px;height:32px;line-height:32px;text-align:center;background:var(--blue-btn);color:var(--white);font-size:12px;font-weight:600}

/* hero */
.hero{left:0;top:108px;width:1200px;height:493px;overflow:hidden}
.hero-photo{position:absolute;inset:0;background:
  linear-gradient(180deg,rgba(255,255,255,.12) 0%,rgba(0,0,0,0) 45%,rgba(60,50,40,.12) 100%),
  linear-gradient(90deg,#cfc9bf 0%,#ddd7cc 22%,#d9c6aa 42%,#dcb58a 56%,#c9b6a0 70%,#a69a8d 86%,#8c8177 100%)}
.hero-arrow{position:absolute;top:210px;width:32px;height:32px;border-radius:50%;background:rgba(80,80,80,.55)}
.search-panel{position:absolute;left:764px;top:46px;width:296px;height:393px;background:rgba(70,70,70,.78);color:var(--white);padding:18px 24px}
.search-title{font-size:22px;font-weight:400;text-align:center;letter-spacing:.5px}
.search-label{font-size:9px;font-weight:700;text-transform:uppercase;margin-top:6px}
.format-grid{display:grid;grid-template-columns:1fr 1fr;row-gap:8px;margin:16px 0 0 0;font-size:10px}
.format-grid span::before{content:"";display:inline-block;width:8px;height:8px;background:var(--white);margin-right:8px;vertical-align:-1px}
.rule{height:1px;background:rgba(255,255,255,.35);margin:14px 0 10px}
.select{height:25px;border:1px solid #ddd;background:rgba(90,90,90,.6);font-size:9px;line-height:23px;padding-left:10px;position:relative;margin-top:6px}
.select::after{content:"";position:absolute;right:10px;top:10px;border:4px solid transparent;border-top:5px solid var(--white)}
.select.keyword::after{display:none}
.gap{height:12px}
.search-submit{display:block;width:144px;height:32px;line-height:32px;margin:22px auto 0;background:var(--blue-btn);text-align:center;font-size:11px;font-weight:600}

/* welcome */
.welcome{left:0;top:624px;width:1200px;text-align:center}
.welcome h2{font-size:18px;font-weight:600;color:#555}
.divider{position:relative;width:720px;height:14px;margin:16px auto 0}
.divider::before,.divider::after{content:"";position:absolute;top:7px;width:340px;height:1px;background:#ddd}
.divider::before{left:0}.divider::after{right:0}
.divider svg{position:absolute;left:349px;top:0}
.welcome p{width:920px;margin:22px auto 0;font-size:12px;line-height:25px;color:var(--muted)}

/* sections */
.section-title{position:absolute;left:0;width:1200px;text-align:center;font-size:21px;font-weight:600;color:#333}
.section-title em{font-style:normal;color:var(--blue)}
.card{position:absolute;width:228px;height:276px;background:var(--card);text-align:center}
.card-photo{height:140px}
.card h3{margin-top:18px;font-size:15px;font-weight:600;color:var(--blue)}
.card p{font-size:12px;color:#666;line-height:24px;margin-top:2px}
.card-btn{display:inline-block;margin-top:10px;height:26px;line-height:26px;padding:0 10px;background:var(--btn-dark);color:var(--white);font-size:10px;font-weight:700}
.card-btn.primary{background:var(--blue-btn)}
.launch-band{left:0;top:1459px;width:1200px;height:408px;background:var(--band)}
.carousel-dot{position:absolute;top:1491px;width:18px;height:18px;border-radius:50%;background:#4a4a4a}
.carousel-dot svg{display:block}

/* enquiry */
.enquiry{left:0;top:1867px;width:1200px;height:204px;background:var(--enquiry);color:var(--white)}
.enquiry h2{position:absolute;top:28px;width:1200px;text-align:center;font-size:22px;font-weight:600}
.enquiry h3{position:absolute;top:66px;width:1200px;text-align:center;font-size:14px;font-weight:600}
.field{position:absolute;top:126px;width:242px;height:38px;border:1px solid #8a8a8a;font-size:10px;font-weight:600;line-height:36px;padding-left:14px}
.enquiry-submit{position:absolute;left:953px;top:124px;width:147px;height:42px;background:var(--white);color:#222;font-size:15px;font-weight:700;line-height:42px;text-align:center}

/* footer */
.site-footer{left:0;top:2071px;width:1200px;height:246px;background:var(--footer);color:var(--footer-text)}
.f-col{position:absolute;top:25px;font-size:11.5px;line-height:22px}
.f-col h4{font-size:12px;font-weight:600;color:#ddd;margin-bottom:18px}
.social{display:flex;gap:22px;margin-bottom:12px}
.social span{width:12px;height:12px;border-radius:50%;background:#ccc}
.post{margin-bottom:20px}
.post a{color:#ccc;display:block}
.post small{font-size:10.5px;color:var(--blue)}
.comment{width:165px;background:#2c2c2c;padding:10px 16px;margin-bottom:22px;line-height:22px}
.tweet{padding-left:22px;position:relative}
.tweet::before{content:"";position:absolute;left:0;top:6px;width:12px;height:12px;border-radius:50%;background:#888}
.footer-base{left:0;top:2317px;width:1200px;height:67px;background:var(--footer-base);color:#aaa;font-size:11px}
.footer-base .copy{position:absolute;left:98px;top:24px}
.footer-base .links{position:absolute;right:100px;top:24px}
</style>
</head>
<body>

<header class="site-header abs">
  <div class="brand abs"><span class="brand-dot"></span><span class="brand-name">lotstallmart.com</span></div>
  <div class="brand-tag abs">INDIA'S LEADING PORTAL FOR RETAIL SPACE</div>
  <nav class="main-nav abs">
    <span class="nav-link active" style="left:508px">HOME</span>
    <span class="nav-link" style="left:585px">ADVERTISE WITH US</span>
    <span class="nav-link" style="left:737px">LISTINGS ALERT</span>
    <span class="nav-link" style="left:861px">MART WIZARDS</span>
    <span class="nav-login">ADVERTISER LOGIN</span>
  </nav>
</header>

<section class="hero abs">
  <div class="hero-photo" role="img" aria-label="Banner photo: happy shopper with colourful shopping bags in a bright mall"></div>
  <span class="hero-arrow" style="left:100px"><svg width="32" height="32"><path d="M18 10l-6 6 6 6" stroke="#fff" stroke-width="2" fill="none"/></svg></span>
  <span class="hero-arrow" style="left:1068px"><svg width="32" height="32"><path d="M14 10l6 6-6 6" stroke="#fff" stroke-width="2" fill="none"/></svg></span>
  <form class="search-panel">
    <div class="search-title">SEARCH CRITERIA</div>
    <div class="search-label" style="margin-top:4px">Select retail format: Meaning of Retail Format</div>
    <div class="format-grid">
      <span>Retail Malls</span><span>Shopping Complex</span>
      <span>High Street Shops</span><span>Retail Warehous</span>
    </div>
    <div class="rule"></div>
    <div class="search-label">Sale or rent or both</div>
    <div class="select">Select here</div>
    <div class="gap"></div>
    <div class="select">Select here</div>
    <div class="search-label" style="margin-top:16px">Select locality/micro-market</div>
    <div class="select">Select here</div>
    <div class="search-label" style="margin-top:16px">Enter keywords:</div>
    <div class="select keyword" style="margin-top:12px"></div>
    <span class="search-submit">SUBMIT HERE</span>
  </form>
</section>

<section class="welcome abs">
  <h2>WELCOME TO OUR COMPANY</h2>
  <div class="divider"><svg width="22" height="14"><path d="M4 12L10 2M9 12L15 2M14 12L20 2" stroke="#bbb" stroke-width="1.2"/></svg></div>
  <p>At vero eos et accusamus et iusto odio dignissimos ducimus qui blanditiis praesentium voluptatum deleniti atque corrupti quos dolores et quas molestias excepturi sint occaecati cupiditate non provident, similique sunt in culpa qui officia</p>
</section>

<h2 class="section-title" style="top:781px">FEATURED RETAIL <em>PROJECTS</em></h2>

<article class="card" style="left:98px;top:837px"><div class="card-photo" role="img" aria-label="Shopper holding a fan of colourful bags" style="background:linear-gradient(135deg,#d9d9d9,#b7b0a8 50%,#e8a43a 80%,#49a56b)"></div><h3>Retail Malls</h3><p>Vela 81 High Street, Sector-81<br>Faridabad</p><span class="card-btn primary">VIEW THE LISTING</span></article>
<article class="card" style="left:356px;top:837px"><div class="card-photo" role="img" aria-label="Family shopping beside a sale sign" style="background:linear-gradient(135deg,#9b3a2c,#d9b35a 45%,#7d6b5c)"></div><h3>Retail Malls</h3><p>Vela 81 High Street, Sector-81<br>Faridabad</p><span class="card-btn">VIEW THE LISTING</span></article>
<article class="card" style="left:615px;top:837px"><div class="card-photo" role="img" aria-label="Shopper with bags in a mall corridor" style="background:linear-gradient(135deg,#cfc8bb,#e08a2c 50%,#9b8e80)"></div><h3>Retail Malls</h3><p>Vela 81 High Street, Sector-81<br>Faridabad</p><span class="card-btn">VIEW THE LISTING</span></article>
<article class="card" style="left:874px;top:837px"><div class="card-photo" role="img" aria-label="Shopper in front of blurred city lights" style="background:linear-gradient(135deg,#2c3f7a,#d2522c 50%,#f0b43c)"></div><h3>Retail Malls</h3><p>Vela 81 High Street, Sector-81<br>Faridabad</p><span class="card-btn">VIEW THE LISTING</span></article>

<article class="card" style="left:98px;top:1144px"><div class="card-photo" role="img" aria-label="Colourful shopping bags held at the side" style="background:linear-gradient(90deg,#d6447a,#39a7c9 40%,#f2c63c 70%,#e0602c)"></div><h3>Retail Malls</h3><p>Vela 81 High Street, Sector-81<br>Faridabad</p><span class="card-btn">VIEW THE LISTING</span></article>
<article class="card" style="left:356px;top:1144px"><div class="card-photo" role="img" aria-label="Blurred shoppers in a mall" style="background:linear-gradient(135deg,#8fb1c9,#c9d6de 50%,#5e7f96)"></div><h3>Retail Malls</h3><p>Vela 81 High Street, Sector-81<br>Faridabad</p><span class="card-btn">VIEW THE LISTING</span></article>
<article class="card" style="left:615px;top:1144px"><div class="card-photo" role="img" aria-label="Shopper smiling in a store" style="background:linear-gradient(135deg,#c8b9ab,#e6cdb8 50%,#d76f8f)"></div><h3>Retail Malls</h3><p>Vela 81 High Street, Sector-81<br>Faridabad</p><span class="card-btn">VIEW THE LISTING</span></article>
<article class="card" style="left:874px;top:1144px"><div class="card-photo" role="img" aria-label="Busy street with shoppers carrying bags" style="background:linear-gradient(135deg,#d9d9d9,#8a8a8a 50%,#3e3e3e)"></div><h3>Retail Malls</h3><p>Vela 81 High Street, Sector-81<br>Faridabad</p><span class="card-btn">VIEW THE LISTING</span></article>

<div class="launch-band abs"></div>
<h2 class="section-title" style="top:1485px">FEATURED NEW <em>LAUNCHES</em></h2>
<span class="carousel-dot" style="left:1060px"><svg width="18" height="18"><path d="M10.5 5l-4 4 4 4" stroke="#fff" stroke-width="1.8" fill="none"/></svg></span>
<span class="carousel-dot" style="left:1082px"><svg width="18" height="18"><path d="M7.5 5l4 4-4 4" stroke="#fff" stroke-width="1.8" fill="none"/></svg></span>

<article class="card" style="left:98px;top:1541px;background:#f7f7f7"><div class="card-photo" role="img" aria-label="Shopper holding bags in a bright store" style="background:linear-gradient(135deg,#e6d5c0,#d88a3c 55%,#c23a5c)"></div><h3>Retail Malls</h3><p>Vela 81 High Street, Sector-81<br>Faridabad</p><span class="card-btn">VIEW THE LISTING</span></article>
<article class="card" style="left:356px;top:1541px;background:#f7f7f7"><div class="card-photo" role="img" aria-label="Customer receiving a pink shopping bag at a counter" style="background:linear-gradient(135deg,#e2ddd5,#e06a9a 50%,#b3a89a)"></div><h3>Retail Malls</h3><p>Vela 81 High Street, Sector-81<br>Faridabad</p><span class="card-btn">VIEW THE LISTING</span></article>
<article class="card" style="left:615px;top:1541px;background:#f7f7f7"><div class="card-photo" role="img" aria-label="Couple browsing clothes on a rack" style="background:linear-gradient(135deg,#3c3d48,#8a7c74 50%,#5a6676)"></div><h3>Retail Malls</h3><p>Vela 81 High Street, Sector-81<br>Faridabad</p><span class="card-btn">VIEW THE LISTING</span></article>
<article class="card" style="left:874px;top:1541px;background:#f7f7f7"><div class="card-photo" role="img" aria-label="Couple shopping together with bags" style="background:linear-gradient(135deg,#cdbfb2,#b98a6c 50%,#d65a7a)"></div><h3>Retail Malls</h3><p>Vela 81 High Street, Sector-81<br>Faridabad</p><span class="card-btn">VIEW THE LISTING</span></article>

<section class="enquiry abs">
  <h2>GET A ENQUIRY FOR FREE</h2>
  <h3>NEWSLETTER</h3>
  <div class="field" style="left:98px">Name</div>
  <div class="field" style="left:381px;padding-left:38px"><svg class="abs" style="left:13px;top:13px" width="13" height="10"><rect x=".5" y=".5" width="12" height="9" fill="none" stroke="#ccc"/><path d="M.5 .5l6 5 6-5" fill="none" stroke="#ccc"/></svg>E-mail</div>
  <div class="field" style="left:672px">Phone</div>
  <span class="enquiry-submit">SUBMIT</span>
</section>

<footer class="site-footer abs">
  <div class="f-col" style="left:98px;width:270px">
    <h4>KEEP IN TOUCH</h4>
    <div class="social"><span></span><span></span><span></span><span></span><span></span><span></span></div>
    <p>Lorem ipsum dolor sit amet, consectetur adipiscing elit. Maecenas non magna. Mattis purus sit amet fermentum.</p>
    <p style="margin-top:20px">Maecenas sed diam eget risus varius blandit sit amet non magna.</p>
  </div>
  <div class="f-col" style="left:413px">
    <h4>RECENT POSTS</h4>
    <div class="post"><a>Another Standard Post Type</a><small>Jan 3 , 2015</small></div>
    <div class="post"><a>Another Standard Post Type</a><small>Jan 3 , 2015</small></div>
    <div class="post"><a>Another Standard Post Type</a><small>Jan 3 , 2015</small></div>
  </div>
  <div class="f-col" style="left:637px">
    <h4>RECENT COMMENTS</h4>
    <div class="comment">Lorem ipsum dolor sit amet, adipiscing</div>
    <div class="comment">Lorem ipsum dolor sit amet, adipiscing</div>
  </div>
  <div class="f-col" style="left:877px;width:240px">
    <h4>LATEST TWEETS</h4>
    <p class="tweet">RT @marketfolk: Attending the Regional Market Makers Annual Meetup - http://lk.to/R81mQ2vTpa http://lk.to/K4wZs9BnEe December 15, 2014 - 1:08 am</p>
  </div>
</footer>

<div class="footer-base abs">
  <span class="copy">©2014 lot stall. all right reserved</span>
  <span class="links">Home &nbsp;/&nbsp; Terms of Use &amp; Privacy Policy &nbsp;/&nbsp; Contact us</span>
</div>

</body>
</html>
```